Corporate Business Card

Very professional, Modern, Not to busy, include phone address email, website
(253) 617-4930, 18761 52nd Avenue S, Kent, WA 98047, martin@plumlinegroup.com, varkoworks.com

Target Market(s)

Manufacturing

Industry/Entity Type

Aero, machining, manufacturing, Off road racing

Contact Information for Business Card

Phone, address email, website

```html
<!DOCTYPE html>
<html lang="en">
<head>
<meta charset="utf-8">
<title>Varko Works – Business Card</title>
<link rel="stylesheet" href="https://fonts.googleapis.com/css2?family=Michroma&family=Roboto:wght@400;700&display=swap">
<style>
  :root {
    --backdrop: #2b2b2b;
    --navy: #2a3766;
    --navy-ink: #27376b;
    --red: #c1272d;
    --white: #f2f2f2;
    --card-light: #ececec;
  }
  html, body {
    margin: 0;
    padding: 0;
    width: 1200px;
    height: 1138px;
    overflow: hidden;
    background: var(--backdrop);
  }
  .canvas {
    position: relative;
    width: 1200px;
    height: 1138px;
  }
  .card {
    position: absolute;
    left: 275px;
    width: 621px;
    height: 375px;
    border-radius: 16px;
    box-shadow: 0 6px 14px rgba(0,0,0,0.45);
  }
  .card-front {
    top: 186px;
    background: var(--navy);
  }
  .card-back {
    top: 608px;
    background: linear-gradient(180deg, #f1f1f1 0%, #e9e9e9 70%, #dedede 100%);
  }
  .brand-name {
    position: absolute;
    left: 0;
    right: 0;
    top: 132px;
    text-align: center;
    font-family: "Roboto", sans-serif;
    font-weight: 700;
    font-size: 66px;
    letter-spacing: 2px;
    color: var(--white);
    line-height: 1;
  }
  .front-web {
    position: absolute;
    left: 0;
    right: 0;
    top: 326px;
    text-align: center;
    font-family: "Roboto", sans-serif;
    font-size: 16px;
    letter-spacing: 13px;
    color: var(--white);
    line-height: 1;
    padding-left: 13px;
  }
  .front-web .accent { color: var(--red); }
  .person-name {
    position: absolute;
    left: 0;
    right: 0;
    top: 114px;
    text-align: center;
    font-family: "Michroma", sans-serif;
    font-size: 27px;
    line-height: 1;
    color: var(--navy-ink);
    margin: 0;
  }
  .person-name .surname { color: var(--red); }
  .contact {
    position: absolute;
    left: 0;
    right: 0;
    top: 155px;
    text-align: center;
    font-family: "Roboto", sans-serif;
    font-size: 17px;
    color: var(--navy-ink);
    line-height: 24.5px;
    margin: 0;
  }
  .contact .address { display: block; margin-top: 8px; }
</style>
</head>
<body>
<div class="canvas">
  <section class="card card-front">
    <div class="brand-name">VARKO WORKS</div>
    <div class="front-web">www.varko<span class="accent">works</span>.com</div>
  </section>
  <section class="card card-back">
    <h1 class="person-name">MARTIN <span class="surname">HALE</span></h1>
    <p class="contact">
      <span>(253) 617-4930</span><br>
      <span>martin@plumlinegroup.com</span><br>
      <span>www.varkoworks.com</span><br>
      <span class="address">18761 52nd Avenue S, Kent, WA 98047</span>
    </p>
  </section>
</div>
</body>
</html>
```